Product label for herbal salves, lotions, soaps and tinctures

We need a very simple, clean and organic looking label that can be used for an ointment jar, a lotion bottle and a dropper bottle.
We have an existing logo (see attached). We like the colors white, olive green, gold and black. It needs to include product name as dominant and logo. It also needs to include an ingredient list, and usage statement. Include weight of product, distributed by, made in the USA, and QVX statement.
Example of what needs to be present:
Logo
Name: Tranquil Ease Blend
Used for: For Muscle Aches, Arthritis, Tendonitis, Headaches
To Use: For muscle aches, arthritis and tendonitis, massage into affected area. For tension headache apply to neck, temples and forehead.
Store in a cool and dry place, away from direct heat and sunlight.
Weight of product: 1.75
DIST. BY: Copper Brook Herbal
Made in the USA
This product is not intended to diagnose, treat, cure
or prevent any disease. Not regulated
by the QVX. Please consult your health care practitioner
before using product. Discontinue use if any adverse reaction occurs.
Ingredient list:
Wildcrafted Ingredients:
Ashwagandha Root, Peppermint Leaf, Hops Flowers, St. John’s Wort Herb, Arnica Flowers, Green Tea Leaf, Alfalfa Leaf, Dandelion Root, Burdock Root, Chickweed Herb, Chaparral Leaf, Yarrow Flowers, Boneset Herb, Moringa Leaf, Meadowsweet Herb, Nettle Leaf
Organic Ingredients:
Olive Oil, Aloe Leaf, Sweet Birch Bark, Helichrysum Flowers, Holy Basil Leaf, Borage Herb, Ginger Root, Angelica Root, White Willow Bark, Mustard Seed, Beeswax, Vitamin E, Essential Oils
Dimensions of Jar:
Circumference: 7 in.
Height: 1 in.

```html
<!DOCTYPE html>
<html lang="en">
<head>
<meta charset="utf-8">
<title>Tranquil Ease Blend – Jar Label</title>
<link rel="stylesheet" href="https://fonts.googleapis.com/css2?family=Ubuntu:wght@400;500;700&family=Bitter:wght@800&display=swap">
<style>
  :root {
    --backdrop: #727845;
    --label-white: #ffffff;
    --olive: #66702f;
    --olive-dark: #4f5a22;
    --gold: #d39a35;
    --ink: #3e4a1c;
    --sprig-light: #e7ecd6;
    --sprig-mid: #c9d3a6;
  }
  * { box-sizing: border-box; margin: 0; padding: 0; }
  html, body { width: 1200px; height: 786px; overflow: hidden; }
  body {
    background: var(--backdrop);
    font-family: "Ubuntu", "Helvetica Neue", Arial, sans-serif;
    color: var(--olive);
  }
  .label {
    position: absolute;
    left: 30px; top: 298px;
    width: 1140px; height: 190px;
    background: var(--label-white);
    overflow: hidden;
  }
  .botanical-band {
    position: absolute;
    left: 250px; top: 100px;
    width: 660px; height: 90px;
    background: radial-gradient(ellipse at 60% 90%, var(--sprig-mid) 0%, var(--sprig-light) 45%, rgba(255,255,255,0) 75%);
    opacity: 0.8;
  }
  .ingredients {
    position: absolute;
    left: 27px; top: 16px;
    width: 320px;
    font-size: 10px;
    line-height: 11.7px;
    letter-spacing: 0.15px;
  }
  .ingredients .heading { font-weight: 500; }
  .ingredients .group { color: var(--gold); font-weight: 500; }
  .footer-info {
    position: absolute;
    left: 27px; top: 143px;
    font-size: 10px; line-height: 11.7px;
    display: flex; gap: 24px;
  }
  .footer-info .distributor strong { font-weight: 700; display: block; }
  .brand {
    position: absolute;
    left: 370px; top: 44px;
    width: 150px;
    display: flex; flex-direction: column; align-items: flex-start; gap: 6px;
  }
  .brand-dot { width: 16px; height: 16px; border-radius: 50%; background: var(--olive); }
  .brand-name {
    font-family: "Ubuntu", "Helvetica Neue", Arial, sans-serif;
    font-weight: 700; font-size: 24px; line-height: 25px;
    color: var(--olive);
  }
  .product-name {
    position: absolute;
    left: 551px; top: 36px;
    font-family: "Bitter", Georgia, serif;
    font-weight: 800;
    font-size: 34px; line-height: 36px;
    color: var(--gold);
    letter-spacing: 0.5px;
  }
  .net-weight {
    position: absolute;
    left: 555px; top: 117px;
    background: var(--olive);
    color: #fff;
    font-size: 11.5px;
    padding: 1px 7px;
    line-height: 15px;
  }
  .usage {
    position: absolute;
    left: 869px; top: 24px;
    width: 250px;
    font-size: 10px; line-height: 11.8px;
    color: var(--olive);
  }
  .usage .title { font-weight: 400; }
  .usage .directions { font-weight: 700; margin-bottom: 5px; }
</style>
</head>
<body>
  <main class="label">
    <div class="botanical-band" role="img" aria-label="Hand-drawn olive branch and herb sprigs in soft green line art along the lower edge"></div>

    <section class="ingredients">
      <p class="heading">Ingredient list:</p>
      <p class="group">Wildcrafted Ingredients:</p>
      <p>Ashwagandha Root, Peppermint Leaf, Hops Flowers, St. John’s Wort Herb, Arnica Flowers, Green Tea Leaf, Alfalfa Leaf, Dandelion Root, Burdock Root, Chickweed Herb, Chaparral Leaf, Yarrow Flowers, Boneset Herb, Moringa Leaf, Meadowsweet Herb, Nettle Leaf</p>
      <p class="group">Organic Ingredients:</p>
      <p>Olive Oil, Aloe Leaf, Sweet Birch Bark, Helichrysum Flowers, Holy Basil Leaf, Borage Herb, Ginger Root, Angelica Root, White Willow Bark, Mustard Seed, Beeswax, Vitamin E, Essential Oils</p>
    </section>

    <section class="footer-info">
      <p class="distributor">Distributed by:<strong>Copper Brook Herbal</strong><strong>Made in the USA</strong></p>
      <p class="storage">Store in a cool and dry place,<br>away from direct heat and sunlight.</p>
    </section>

    <div class="brand">
      <span class="brand-dot"></span>
      <span class="brand-name">Copper Brook<br>Herbal</span>
    </div>

    <h1 class="product-name">Tranquil Ease<br>Blend</h1>
    <span class="net-weight">1.75 oz</span>

    <section class="usage">
      <p class="title">How to Use</p>
      <p class="directions">For muscle aches, arthritis and tendonitis, massage into affected area.<br>For tension headache apply to neck, temples and forehead.</p>
      <p>This product is not intended to diagnose, treat, cure or prevent any disease.<br>Not regulated by the QVX.<br>Please consult your health care practitioner before using product.<br>Discontinue use if any adverse reaction occurs.</p>
    </section>
  </main>
</body>
</html>
```